Manifesto

I want a manifesto with the following five manifestos for our Not for Profit

- We are a For-purpose organisation
- Every service we offer is free
- Every product we sell funds our services
- Every financial transaction is transparent
- Our service is for the greater good
- Our purpose is always to serve the people
- We are a for purpose organisation

Its to go with this website logo/look/feel www.brightharbour.co.nz

Two attachments:

1. I quite like this look/feel of a manifesto (see attached), I want something clean, professional but I also quite like either Retro modern look feel also like a fresh, and uplifting as its for sick people coming to see us and our funds where anyone buys a product are used for helping those who are sick with healing......so needs something conveyed that is fresh, uplifing yet professional.
2. This attachment is how I wrote this down when inspired of how I wanted Bright Harbour to operate. This is our values chart. It has to say

Also check out our website for our logo, look etc.. it doesnt have to be the same but red somewhere would link back to logo. www.brightharbour.co.nz .

Industry/Entity Type

Financial

```html
<!DOCTYPE html>
<html lang="en">
<head>
<meta charset="utf-8">
<title>Bright Harbour Manifesto</title>
<link rel="stylesheet" href="https://fonts.googleapis.com/css2?family=Arvo:wght@700&family=Lobster+Two:ital,wght@1,700&family=Montserrat:wght@800&family=Roboto:wght@400&display=swap">
<style>
  :root {
    --backdrop: #ececec;
    --stone-light: #9a9a9a;
    --stone-mid: #858585;
    --stone-dark: #6e6e6e;
    --maroon: #3d0a12;
    --ivory: #ffffff;
    --ink: #111111;
    --shadow: rgba(35, 4, 8, 0.75);
  }
  * { margin: 0; padding: 0; box-sizing: border-box; }
  html, body {
    width: 1200px; height: 1000px; overflow: hidden;
    background: var(--backdrop);
  }
  .poster {
    position: absolute; left: 276px; top: 53px;
    width: 634px; height: 899px;
    background:
      radial-gradient(ellipse at 30% 25%, var(--stone-light), transparent 60%),
      radial-gradient(ellipse at 75% 70%, var(--stone-light), transparent 55%),
      linear-gradient(160deg, var(--stone-mid), var(--stone-dark));
  }
  .line {
    position: absolute; white-space: nowrap; line-height: 1;
  }
  .slab { font-family: "Arvo", Georgia, serif; font-weight: 700; }
  .script { font-family: "Lobster Two", "Brush Script MT", cursive; font-style: italic; font-weight: 700; }
  .geo { font-family: "Montserrat", Arial, sans-serif; font-weight: 800; }
  .maroon { color: var(--maroon); }
  .ivory { color: var(--ivory); text-shadow: 2px 2px 0 var(--shadow); }

  .divider { position: absolute; left: 22px; width: 590px; height: 6px; }

  .footer-title { position: absolute; left: 0; width: 634px; text-align: center; top: 845px;
    font-size: 17px; color: var(--ink); }
  .footer-url { position: absolute; left: 0; width: 634px; text-align: center; top: 871px;
    font-family: "Roboto", Arial, sans-serif; font-size: 12px; letter-spacing: 2.4px; color: var(--ivory); }
</style>
</head>
<body>
<main class="poster" aria-label="Bright Harbour manifesto">
  <!-- Row 1 -->
  <div class="line slab maroon" style="left:22px; top:22px; font-size:55px; letter-spacing:-1px;">WE ARE A</div>
  <div class="line slab ivory" style="left:23px; top:82px; font-size:39px; letter-spacing:0.5px;">FOR PURPOSE</div>
  <div class="line slab maroon" style="left:23px; top:126px; font-size:33px; letter-spacing:0.3px;">ORGANISATION</div>

  <div class="line script ivory" style="left:372px; top:26px; font-size:40px;">Every Service</div>
  <div class="line slab maroon" style="left:380px; top:70px; font-size:22px; letter-spacing:6.5px;">we offer is</div>
  <div class="line slab maroon" style="left:374px; top:88px; font-size:76px; letter-spacing:7px;">FREE</div>

  <svg class="divider" style="top:177px;" viewBox="0 0 590 6" preserveAspectRatio="none" aria-hidden="true">
    <path d="M0 3 Q295 -1 590 3 Q295 7 0 3 Z" fill="var(--maroon)"/>
  </svg>

  <!-- Row 2 -->
  <div class="line slab ivory" style="left:21px; top:195px; font-size:64px; letter-spacing:0.5px;">EVERY PRODUCT</div>
  <div class="line slab maroon" style="left:22px; top:260px; font-size:34px; letter-spacing:0.6px;">we sell funds our services</div>

  <svg class="divider" style="top:312px;" viewBox="0 0 590 6" preserveAspectRatio="none" aria-hidden="true">
    <path d="M0 3 Q295 -1 590 3 Q295 7 0 3 Z" fill="var(--maroon)"/>
  </svg>

  <!-- Row 3 -->
  <div class="line slab ivory" style="left:20px; top:340px; font-size:50px; letter-spacing:17px;">EVERY</div>
  <div class="line slab ivory" style="left:21px; top:400px; font-size:29px; letter-spacing:8.5px;">FINANCIAL</div>
  <div class="line slab maroon" style="left:21px; top:436px; font-size:25px; letter-spacing:4.6px;">TRANSACTION</div>
  <div class="line slab maroon" style="left:21px; top:466px; font-size:23px; letter-spacing:4.2px;">is transparent</div>

  <div class="line slab maroon" style="left:338px; top:346px; font-size:23px; letter-spacing:1.6px;">OUR SERVICE IS</div>
  <div class="line script ivory" style="left:338px; top:370px; font-size:43px;">for the greater</div>
  <div class="line geo ivory" style="left:346px; top:422px; font-size:78px; letter-spacing:-1px;">GOOD</div>

  <svg class="divider" style="top:514px;" viewBox="0 0 590 6" preserveAspectRatio="none" aria-hidden="true">
    <path d="M0 3 Q295 -1 590 3 Q295 7 0 3 Z" fill="var(--maroon)"/>
  </svg>

  <!-- Row 4 -->
  <div class="line slab maroon" style="left:21px; top:540px; font-size:55px; letter-spacing:3.4px;">OUR PURPOSE IS</div>
  <div class="line script ivory" style="left:24px; top:594px; font-size:52px;">always to serve the people</div>

  <svg class="divider" style="top:674px;" viewBox="0 0 590 6" preserveAspectRatio="none" aria-hidden="true">
    <path d="M0 3 Q295 -1 590 3 Q295 7 0 3 Z" fill="var(--maroon)"/>
  </svg>

  <!-- Row 5 -->
  <div class="line slab maroon" style="left:21px; top:697px; font-size:42px; letter-spacing:1.6px;">WE ARE A FOR PURPOSE</div>
  <div class="line script ivory" style="left:22px; top:738px; font-size:104px;">organisation</div>

  <div class="footer-title script">Bright Harbour Manifesto</div>
  <div class="footer-url">www.brightharbour.co.nz</div>
</main>
</body>
</html>
```